Re-style home page - eye-catching and unique design for social commerce website

We need a new concept design for BrinoKet's home page.
We don't want to make huge changes but creating a more professional and eye-catching style.

We need to look very serious like a professional services company and in the same time to look like a social network for e-commerce.

Our logo is very captive and you can use to creating something of harmonious.

This is a re-style and I'm excepted to see unique and fresh design like Glimmora.

Target Market(s)

e-commerce and social

Industry/Entity Type

Social

Number of Pages Required

1 page

Font styles to use
Serif
Sans Serif

Requirements
Must have
• An eye-catching result.
• Search bar with logo and Login How it works and business
• The slogan with login and signup.
• Footer links.
Nice to have
• I would like to open the home page and see only two clear ways:
• -Consumer
• --Search
• --The slogan
• --Login and Signup
• --How it works
• -Business
• --Go to Business area
• Background: City, Shopping.
Should not have
• Scrollbar style!

```html
<!DOCTYPE html>
<html lang="en">
<head>
<meta charset="utf-8">
<title>BrinoKet – Shop directly from your profile</title>
<link rel="stylesheet" href="https://fonts.googleapis.com/css2?family=Montserrat:wght@400;500;600;700&display=swap">
<style>
  :root {
    --ink: #ffffff;
    --ink-soft: rgba(255,255,255,0.72);
    --ink-muted: rgba(255,255,255,0.6);
    --accent: #e8264f;
    --social: #4a64a6;
    --field: #ffffff;
    --field-text: #777777;
    --city-dark: #1c1714;
    --city-mid: #3a2e26;
    --city-warm: #5a4030;
    --card-rose: #c56a5e;
    --card-peach: #d99a7c;
    --card-red: #b8454a;
  }
  * { box-sizing: border-box; margin: 0; padding: 0; }
  html, body { width: 1200px; height: 675px; overflow: hidden; }
  body {
    font-family: "Montserrat", sans-serif;
    color: var(--ink);
    background: var(--city-dark);
    position: relative;
  }
  .city-backdrop {
    position: absolute; inset: 0;
    background:
      radial-gradient(ellipse 520px 420px at 640px 180px, rgba(120,90,70,0.55), transparent 70%),
      radial-gradient(ellipse 300px 300px at 1050px 200px, rgba(110,85,65,0.45), transparent 70%),
      linear-gradient(180deg, var(--city-mid) 0%, var(--city-warm) 35%, var(--city-mid) 65%, var(--city-dark) 100%);
  }
  .brand {
    position: absolute; left: 88px; top: 23px;
    display: flex; align-items: center; gap: 7px;
    font-weight: 600; font-size: 19px; letter-spacing: -0.3px;
  }
  .brand-dot { width: 12px; height: 12px; border-radius: 50%; background: var(--accent); }
  .top-nav { position: absolute; right: 86px; top: 25px; display: flex; align-items: center; gap: 34px; }
  .top-nav .nav-link { font-size: 13px; font-weight: 500; color: var(--ink); text-decoration: none; }
  .btn-login {
    background: var(--accent); color: var(--ink); font-size: 13px; font-weight: 500;
    width: 73px; height: 26px; border-radius: 3px; display: flex; align-items: center; justify-content: center;
    text-decoration: none;
  }
  .hero-card {
    position: absolute; left: 350px; top: 124px; width: 500px; height: 313px;
    border-radius: 11px; overflow: hidden;
  }
  .hero-photo {
    position: absolute; inset: 0;
    background:
      radial-gradient(ellipse 140px 110px at 440px 270px, rgba(120,55,45,0.75), transparent 75%),
      radial-gradient(ellipse 200px 120px at 230px 110px, var(--card-peach), transparent 75%),
      linear-gradient(90deg, var(--card-rose) 0%, var(--card-peach) 45%, var(--card-red) 75%, var(--card-rose) 100%);
  }
  .hero-content { position: relative; text-align: center; }
  .hero-title { margin-top: 57px; font-size: 24px; font-weight: 600; letter-spacing: -0.2px; }
  .hero-tagline { margin-top: 5px; font-size: 14px; font-weight: 500; }
  .auth-row {
    position: absolute; left: 61px; top: 167px; width: 378px;
    display: flex; align-items: center; justify-content: space-between;
  }
  .btn-social, .btn-signup {
    width: 163px; height: 36px; border-radius: 3px; display: flex; align-items: center; justify-content: center;
    color: var(--ink); text-decoration: none;
  }
  .btn-social { background: var(--social); font-size: 10px; font-weight: 700; gap: 8px; }
  .btn-social .mark { width: 8px; height: 8px; background: var(--ink); border-radius: 50%; }
  .btn-signup { background: var(--accent); font-size: 13px; font-weight: 500; }
  .auth-or { font-size: 12px; color: var(--ink); }
  .search-field {
    position: absolute; left: 61px; top: 226px; width: 378px; height: 41px;
    background: var(--field); border-radius: 3px; border: none;
    padding-left: 15px; font-family: inherit; font-size: 13px; color: var(--field-text);
    display: flex; align-items: center;
  }
  .audience-paths {
    position: absolute; top: 457px; left: 449px; display: flex;
  }
  .path { text-decoration: none; color: var(--ink); }
  .path-title { font-size: 16px; font-weight: 600; line-height: 1; margin-top: 4px; }
  .path-sub { font-size: 10.5px; color: var(--ink-muted); margin-top: 7px; }
  .path-consumer { padding-right: 25px; border-right: 1px solid rgba(255,255,255,0.2); height: 39px; }
  .path-business { padding-left: 27px; }
  .site-footer { position: absolute; left: 0; right: 0; top: 602px; text-align: center; }
  .footer-links { display: flex; justify-content: center; gap: 24px; font-size: 10px; }
  .footer-links a { color: var(--ink-soft); text-decoration: none; }
  .footer-links a.current { color: var(--ink); font-weight: 500; }
  .copyright { margin-top: 16px; font-size: 9.5px; color: var(--ink-muted); }
</style>
</head>
<body>
  <div class="city-backdrop" role="img" aria-label="Blurred busy city shopping street with pedestrians"></div>

  <header>
    <div class="brand"><span>BrinoKet</span><span class="brand-dot"></span></div>
    <nav class="top-nav">
      <a class="nav-link" href="#">How It Works</a>
      <a class="btn-login" href="#">Login</a>
    </nav>
  </header>

  <main>
    <section class="hero-card">
      <div class="hero-photo" role="img" aria-label="Close-up photo of chocolate cupcakes on a warm pink background"></div>
      <div class="hero-content">
        <h1 class="hero-title">Shop directly from your profile</h1>
        <p class="hero-tagline">Save your time. Live better.</p>
      </div>
      <div class="auth-row">
        <a class="btn-social" href="#"><span class="mark"></span>Sign in with Circlebook</a>
        <span class="auth-or">or</span>
        <a class="btn-signup" href="#">Sign Up</a>
      </div>
      <div class="search-field">Search or Setup your feed</div>
    </section>

    <div class="audience-paths">
      <a class="path path-consumer" href="#">
        <div class="path-title">Consumer</div>
        <div class="path-sub">Go to Consumer area</div>
      </a>
      <a class="path path-business" href="#">
        <div class="path-title">Business</div>
        <div class="path-sub">Go to Business area</div>
      </a>
    </div>
  </main>

  <footer class="site-footer">
    <nav class="footer-links">
      <a class="current" href="#">About Us</a>
      <a href="#">Blog</a>
      <a href="#">Business</a>
      <a href="#">Jobs</a>
      <a href="#">Privacy</a>
      <a href="#">FAQ</a>
      <a href="#">Contacts</a>
    </nav>
    <p class="copyright">© 2015 BrinoKet. All right reserved.</p>
  </footer>
</body>
</html>
```